Last of Tides

Story is a sequel to "Dusk of Copper Rain" which was a trip of an old ship with that name to India at the end of the Flower Power Era. This story is the aftermath of its eventual end in the scrapyard of Formosa. It describes the rather wild return trip of the motley crew from India via |Formosa back to the US with the dramatic undertone that the maritime industry is changing from the traditional break-bulk cargo transport to the modern method of container transport. The plot also involves a heist of thousands of bottles of whisky but that is of lesser concern. Design should be simple, be in the same style (with the original design of a single wilting flower on a beach) to affect its relation to the first book.The last of tides really signiies the end of traditional break-bulk (piecemeal) cargoship transport that had been done for thousands of years.

Target Market(s)

Young Adults and anyone associated with the Maritime Industry

Industry/Entity Type

Maritime industry

Font styles to use
Serif
Sans Serif
Other font styles liked:
• Arial or similar for the title; Serif for Author's name and text on back

Requirements
Must have
• Association with the first book design. Simple but effective design; subdued color scheme
Nice to have
• Totally wilted flower(s); deserted beach; sinking (dargo) ship (1960's); Sea;
Should not have
• Faces and pictures of personns, no complicated designs with lots of detail reflecting the plot; no bright colors

```html
<!DOCTYPE html>
<html lang="en">
<head>
<meta charset="utf-8">
<title>Last of Tides — Book Cover</title>
<link href="https://fonts.googleapis.com/css2?family=Marcellus&family=Cormorant+Garamond:ital,wght@0,600;1,500&display=swap" rel="stylesheet">
<style>
  :root {
    --sky-top: #7b86cc;
    --sky-mid: #a98cc4;
    --sky-pink: #d8a3c2;
    --horizon-glow: #efc0cf;
    --horizon: #c9a4c4;
    --sea-light: #a895b0;
    --sea-mid: #8c7a94;
    --sea-dark: #5e5065;
    --rock: #3a333d;
    --rock-deep: #1f1b21;
    --title: #ffffff;
    --title-shadow: rgba(20, 12, 28, 0.9);
  }
  * { margin: 0; padding: 0; box-sizing: border-box; }
  html, body { width: 800px; height: 1200px; overflow: hidden; background: var(--rock-deep); }
  .cover {
    position: relative;
    width: 800px;
    height: 1200px;
    overflow: hidden;
  }
  .cover-scene {
    position: absolute;
    inset: 0;
    background:
      radial-gradient(ellipse 520px 140px at 120px 470px, rgba(239, 192, 207, 0.7), rgba(239, 192, 207, 0) 75%),
      linear-gradient(180deg,
        var(--sky-top) 0%,
        var(--sky-mid) 14%,
        var(--sky-pink) 28%,
        var(--horizon-glow) 38%,
        var(--horizon) 43%,
        var(--sea-light) 46%,
        var(--sea-light) 56%,
        var(--sea-mid) 64%,
        var(--sea-dark) 72%,
        var(--rock) 82%,
        var(--rock-deep) 100%);
  }
  .cover-title {
    position: absolute;
    left: 0;
    right: 0;
    display: block;
    text-align: center;
    color: var(--title);
    text-shadow: 2px 2px 0 var(--title-shadow);
    font-family: "Marcellus", serif;
    font-weight: 400;
    line-height: 1;
  }
  .title-first {
    top: 104px;
    font-size: 140px;
    letter-spacing: 30px;
    padding-left: 30px;
  }
  .title-joiner {
    top: 256px;
    font-family: "Cormorant Garamond", serif;
    font-style: italic;
    font-weight: 500;
    font-size: 72px;
  }
  .title-last {
    top: 366px;
    font-size: 140px;
    letter-spacing: 26px;
    padding-left: 26px;
  }
  .cover-author {
    position: absolute;
    top: 1082px;
    left: 0;
    right: 0;
    text-align: center;
    color: var(--title);
    text-shadow: 1px 1px 0 var(--title-shadow);
    font-family: "Cormorant Garamond", serif;
    font-weight: 600;
    font-size: 42px;
    letter-spacing: 7px;
    padding-left: 7px;
    line-height: 1;
  }
</style>
</head>
<body>
  <main class="cover">
    <div class="cover-scene" role="img" aria-label="Long-exposure photograph of a wrecked wooden cargo boat stranded in misty shallow sea at dusk, purple and pink sky, dark rocks in the foreground"></div>
    <h1>
      <span class="cover-title title-first">LAST</span>
      <span class="cover-title title-joiner">of</span>
      <span class="cover-title title-last">TIDES</span>
    </h1>
    <p class="cover-author">PIETER VANDERKAMP</p>
  </main>
</body>
</html>
```